Stonebrace Business Card Design

The Stonebrace Co is an aggregate (crushing) equipment dealer serving Western Canadian provinces. Stonebrace is a distributor of aggregate equipment for different manufacturers.

We are looking to change and update the existing business card which has been used since the existence of the company. A copy of existing card has been attached for reference. The Stonebrace Co logo we want to remain the same and we want the green color to remain the same.

We are wanting something new with a different look. A refreshing card to show a new modern and updated look. No longer wanting to have the manufacturers on the back of the card but something more like our logo on the back of the card with a statement like "Crushing Solutions"

ideas could be:
- card can be different colors on front and back
- front or reverse of the card could possibly be the green color with the logo in black

Target Market(s)

Owners of Aggregate/Crushing companies

Contact Information for Business Card

see above

Requirements
Must have
• - logo to remain same along with same font within logo
• - green color to remain same
Nice to have
• as noted above under project description
Should not have

```html
<!DOCTYPE html>
<html lang="en">
<head>
<meta charset="utf-8">
<title>Stonebrace Co Business Card</title>
<link rel="stylesheet" href="https://fonts.googleapis.com/css2?family=Montserrat:wght@300;400;500;800&display=swap">
<style>
  :root {
    --olive: #8f8b35;
    --ink: #232021;
    --paper: #ffffff;
    --backdrop: #d9d9d6;
  }
  html, body {
    margin: 0;
    padding: 0;
    width: 1200px;
    height: 1000px;
    overflow: hidden;
    background: var(--backdrop);
    font-family: "Montserrat", sans-serif;
  }
  .canvas {
    position: relative;
    width: 1200px;
    height: 1000px;
  }
  .card {
    position: absolute;
    width: 620px;
    height: 354px;
    background: var(--paper);
    box-shadow: 0 6px 18px rgba(0,0,0,0.18);
    overflow: hidden;
  }
  .card svg.shapes {
    position: absolute;
    inset: 0;
  }
  .card--reverse { left: 90px; top: 120px; }
  .card--front { left: 490px; top: 520px; }

  /* reverse side */
  .brand-mark {
    position: absolute;
    left: 0; right: 0;
    top: 130px;
    display: flex;
    justify-content: center;
    align-items: center;
    gap: 12px;
    color: var(--ink);
    font-weight: 800;
    font-size: 30px;
    letter-spacing: 0.5px;
  }
  .brand-mark .dot {
    width: 22px; height: 22px;
    border-radius: 50%;
    background: var(--olive);
  }
  .tagline {
    position: absolute;
    left: 0; right: 0;
    top: 262px;
    text-align: center;
    color: var(--paper);
    font-weight: 300;
    font-size: 21px;
    letter-spacing: 1px;
  }

  /* front side */
  .front-brand {
    position: absolute;
    right: 34px;
    top: 44px;
    color: var(--paper);
    font-weight: 800;
    font-size: 15px;
    letter-spacing: 0.3px;
  }
  .contact-name {
    position: absolute;
    left: 30px;
    top: 108px;
    color: var(--paper);
    font-weight: 500;
    font-size: 25px;
    letter-spacing: 1px;
  }
  .phones {
    position: absolute;
    left: 30px;
    top: 160px;
    margin: 0;
    padding: 0;
    list-style: none;
  }
  .phones li, .online li {
    display: flex;
    align-items: center;
    gap: 14px;
    color: var(--ink);
    font-weight: 400;
    line-height: 1;
  }
  .phones li { font-size: 20px; height: 24px; letter-spacing: 1px; }
  .online {
    position: absolute;
    left: 372px;
    top: 114px;
    margin: 0;
    padding: 0;
    list-style: none;
  }
  .online li { font-size: 17px; height: 26px; gap: 10px; }
  .icon { width: 16px; height: 16px; flex: none; }
  .address {
    position: absolute;
    left: 256px;
    width: 340px;
    top: 240px;
    text-align: center;
    color: var(--paper);
    font-weight: 500;
    font-size: 12px;
    letter-spacing: 0.6px;
  }
  .services {
    position: absolute;
    left: 0; right: 0;
    top: 296px;
    text-align: center;
    color: var(--paper);
    font-weight: 300;
    font-size: 18px;
    letter-spacing: 1px;
  }
  .services .sep {
    display: inline-block;
    width: 1px;
    height: 24px;
    background: var(--paper);
    margin: 0 12px;
    vertical-align: middle;
  }
</style>
</head>
<body>
<main class="canvas">

  <section class="card card--reverse" aria-label="Card reverse">
    <svg class="shapes" width="620" height="354" viewBox="0 0 620 354" aria-hidden="true">
      <path fill="var(--olive)" d="M140 0 H470 L452 32 Q440 50 418 50 H196 Q174 50 162 32 Z"/>
      <path fill="var(--olive)" d="M152 354 L170 246 Q176 222 202 222 H420 Q446 222 452 246 L470 354 Z"/>
    </svg>
    <div class="brand-mark"><span class="dot"></span><span>THE STONEBRACE CO.</span></div>
    <div class="tagline">CRUSHING SOLUTIONS</div>
  </section>

  <section class="card card--front" aria-label="Card front">
    <svg class="shapes" width="620" height="354" viewBox="0 0 620 354" aria-hidden="true">
      <path fill="var(--olive)" d="M0 0 H620 V100 H378 Q356 100 350 118 L340 148 H0 Z"/>
      <rect fill="var(--ink)" x="0" y="264" width="620" height="90"/>
      <path fill="var(--olive)" d="M250 270 L260 242 Q266 228 286 228 H566 Q584 228 590 242 L600 270 Z"/>
    </svg>

    <div class="front-brand">THE STONEBRACE CO.</div>
    <div class="contact-name">DEREK MALVERN</div>

    <ul class="online">
      <li>
        <svg class="icon" viewBox="0 0 16 16" aria-hidden="true"><rect x="1" y="3" width="14" height="10" fill="var(--ink)"/><path d="M1 3 L8 9 L15 3" stroke="var(--paper)" stroke-width="1.2" fill="none"/></svg>
        derek@stonebr.com
      </li>
      <li>
        <svg class="icon" viewBox="0 0 16 16" aria-hidden="true"><circle cx="8" cy="8" r="6.5" fill="none" stroke="var(--ink)" stroke-width="1.4"/><ellipse cx="8" cy="8" rx="2.8" ry="6.5" fill="none" stroke="var(--ink)" stroke-width="1.2"/><line x1="1.5" y1="8" x2="14.5" y2="8" stroke="var(--ink)" stroke-width="1.2"/></svg>
        www.stonebrace.ca
      </li>
    </ul>

    <ul class="phones">
      <li>
        <svg class="icon" viewBox="0 0 16 16" aria-hidden="true"><path d="M2 6 Q8 1 14 6 L12 8 L10 6.5 H6 L4 8 Z" fill="var(--ink)"/><rect x="3" y="9" width="10" height="5" rx="1" fill="var(--ink)"/></svg>
        780 . 555 . 0142
      </li>
      <li>
        <svg class="icon" viewBox="0 0 16 16" aria-hidden="true"><path d="M4 2 L6.5 2 L7.5 5.5 L6 6.8 Q7.5 9.5 9.2 10 L10.5 8.5 L14 9.5 V12 Q13 14.5 10 14 Q3 11 2 4 Q2 2.5 4 2 Z" fill="var(--ink)"/></svg>
        780 . 555 . 0187
      </li>
      <li>
        <svg class="icon" viewBox="0 0 16 16" aria-hidden="true"><rect x="4" y="1.5" width="8" height="4" fill="var(--ink)"/><rect x="1.5" y="6" width="13" height="6" rx="1" fill="var(--ink)"/><rect x="4" y="10" width="8" height="4.5" fill="var(--ink)" stroke="var(--paper)" stroke-width="0.8"/></svg>
        780 . 555 . 0163
      </li>
    </ul>

    <div class="address">2218-48B AVENUE, NISKU, ALBERTA T9E 7R3</div>
    <div class="services">SCREENERS<span class="sep"></span>CRUSHERS<span class="sep"></span>STACKERS</div>
  </section>

</main>
</body>
</html>
```